New Business Card Design for Manufacturing

We are an engineering/manufacturing company that offers Advanced machining/assembly/engineering services, as well as innovative products for the heavy duty engine cooling markets.

We are looking to get a new business card designed that is clean and modern looking, but still fits the wide range of technical/skilled work we do.

- We hope to use this design as the base for other design work in new Presentations, web, and print work.

Industry/Entity Type

Engineering

Contact Information for Business Card

Our preferred color of blue is (RGB) 22/71/159 but can vary slightly from that color. Our content will be our Logo and full company name (Vantrell Forge Works, Inc.), company address, name, job title, phone number with extension, cell number, fax number, website, and email address on the cards.
We'd like the full company name next to the logo, but we are open to other interpretations of that layout.
Preferably, we would like the back side to be clean with just our logo, and the front to contain all of the contact information.

Colors
2f74b4
0355a3
85abd2

Requirements
Must have
• - Logo, company name, needed content - We are open to interpretation beyond that.
• - Standard size business card.
• - Horizontal orientation.
• - Enough space for lengthy names / job titles (for example, a job title could read "Directory of Human Resources" or "V.P. of Governmental Affairs"). We need this to look clean, whether the title be short (CEO) or long (as described above).

```html
<!DOCTYPE html>
<html lang="en">
<head>
<meta charset="utf-8">
<title>Vantrell Forge Works – Business Card</title>
<link href="https://fonts.googleapis.com/css2?family=Roboto:wght@400;500&family=Roboto+Condensed:wght@500;700&display=swap" rel="stylesheet">
<style>
  :root {
    --brand-blue: #0f52a0;
    --brand-blue-deep: #0d4f9e;
    --paper: #f2f2f2;
    --ink: #1a1a1a;
    --ink-soft: #555555;
    --backdrop: #2b2b2b;
  }
  html, body {
    margin: 0;
    padding: 0;
    width: 1200px;
    height: 960px;
    overflow: hidden;
    background: var(--backdrop);
  }
  .canvas {
    position: relative;
    width: 1200px;
    height: 960px;
  }
  .card {
    position: absolute;
    width: 600px;
    height: 343px;
    box-sizing: border-box;
    overflow: hidden;
  }
  /* Front */
  .card-front {
    left: 314px;
    top: 113px;
    background: var(--paper);
  }
  .card-front .accent-tab {
    position: absolute;
    left: 0;
    top: 50px;
    width: 15px;
    height: 40px;
    background: var(--brand-blue);
  }
  .card-front .base-band {
    position: absolute;
    left: 0;
    bottom: 0;
    width: 100%;
    height: 14px;
    background: var(--brand-blue);
  }
  .person {
    position: absolute;
    left: 52px;
    top: 50px;
  }
  .person-name {
    margin: 0;
    font-family: "Roboto Condensed", sans-serif;
    font-weight: 500;
    font-size: 23px;
    line-height: 26px;
    color: var(--brand-blue);
    letter-spacing: 0.2px;
  }
  .person-title {
    margin: 1px 0 0;
    font-family: "Roboto", sans-serif;
    font-size: 14px;
    line-height: 17px;
    color: var(--ink);
  }
  .address {
    position: absolute;
    left: 52px;
    top: 168px;
    margin: 0;
    font-family: "Roboto", sans-serif;
    font-style: normal;
    font-size: 14px;
    line-height: 18px;
    color: var(--ink-soft);
  }
  .contact-list {
    position: absolute;
    left: 52px;
    top: 215px;
    margin: 0;
    padding: 0;
    list-style: none;
    font-family: "Roboto", sans-serif;
    font-size: 14px;
    line-height: 19px;
    color: var(--ink-soft);
  }
  .contact-list li {
    display: flex;
    align-items: center;
    gap: 8px;
  }
  .contact-list svg {
    width: 13px;
    height: 13px;
    fill: var(--brand-blue);
    flex: none;
  }
  .front-wordmark {
    position: absolute;
    right: 50px;
    top: 214px;
    display: flex;
    align-items: center;
    gap: 10px;
    font-family: "Roboto Condensed", sans-serif;
    font-weight: 700;
    font-size: 26px;
    line-height: 30px;
    color: var(--brand-blue);
  }
  .mark-square {
    width: 22px;
    height: 22px;
    background: currentColor;
    flex: none;
  }
  /* Back */
  .card-back {
    left: 311px;
    top: 472px;
    background: var(--brand-blue-deep);
    display: flex;
    align-items: center;
    justify-content: center;
  }
  .back-wordmark {
    display: flex;
    align-items: center;
    gap: 14px;
    font-family: "Roboto Condensed", sans-serif;
    font-weight: 700;
    font-size: 38px;
    line-height: 44px;
    color: #ffffff;
  }
  .back-wordmark .mark-square {
    width: 30px;
    height: 30px;
  }
</style>
</head>
<body>
<main class="canvas">
  <section class="card card-front" aria-label="Business card front">
    <span class="accent-tab"></span>
    <div class="person">
      <h1 class="person-name">DORIAN HALVEK</h1>
      <p class="person-title">V.P. of Governmental Affairs</p>
    </div>
    <address class="address">4120 Larkspur Court<br>Fairbanks, Alaska 99712</address>
    <ul class="contact-list">
      <li>
        <svg viewBox="0 0 24 24" aria-hidden="true"><path d="M6.6 10.8a15.1 15.1 0 0 0 6.6 6.6l2.2-2.2a1 1 0 0 1 1-.25 11.4 11.4 0 0 0 3.6.57 1 1 0 0 1 1 1V20a1 1 0 0 1-1 1A17 17 0 0 1 3 4a1 1 0 0 1 1-1h3.5a1 1 0 0 1 1 1c0 1.25.2 2.45.57 3.57a1 1 0 0 1-.25 1z"/></svg>
        555 214 7380
      </li>
      <li>
        <svg viewBox="0 0 24 24" aria-hidden="true"><path d="M7 1h10a2 2 0 0 1 2 2v18a2 2 0 0 1-2 2H7a2 2 0 0 1-2-2V3a2 2 0 0 1 2-2zm0 3v14h10V4zm5 15.2a1.2 1.2 0 1 0 0 2.4 1.2 1.2 0 0 0 0-2.4z"/></svg>
        555 902 4617
      </li>
      <li>
        <svg viewBox="0 0 24 24" aria-hidden="true"><path d="M2 5h20v14H2zm2 2v.4l8 5 8-5V7zm0 2.8V17h16V9.8l-8 5z"/></svg>
        dorian@vantrell.com
      </li>
      <li>
        <svg viewBox="0 0 24 24" aria-hidden="true"><path d="M12 2a10 10 0 1 0 0 20 10 10 0 0 0 0-20zm-1 17.9A8 8 0 0 1 4.1 10l4.9 5v1a2 2 0 0 0 2 2zm6.9-2.5A2 2 0 0 0 16 16h-1v-3a1 1 0 0 0-1-1H8v-2h2a1 1 0 0 0 1-1V7h2a2 2 0 0 0 2-2v-.4a8 8 0 0 1 2.9 12.8z"/></svg>
        www.vantrell.com
      </li>
    </ul>
    <div class="front-wordmark">
      <span class="mark-square" aria-hidden="true"></span>
      <span>Vantrell Forge Works, Inc.</span>
    </div>
    <span class="base-band"></span>
  </section>

  <section class="card card-back" aria-label="Business card back">
    <div class="back-wordmark">
      <span class="mark-square" aria-hidden="true"></span>
      <span>Vantrell Forge Works, Inc.</span>
    </div>
  </section>
</main>
</body>
</html>
```